Redesign to improve branding visibility and product messaging

Update the logo using the new logo provided attached.
Then, improve product messaging on the packaging, however leaving the colours, general blurbs, and the fruit/nut image outlines as they are (but open to make it simpler).
Please review photos Stockist 1" to 5" and recommend the new style for:
1 Energy Ball Bag
1 Energy Ball Inner Box
1 Cereal Bag
Key features:
1. Allow more transparent window to show more of the product inside.
2. Strong brand presence and clear nutritional call outs - keep in mind we display our products on supermarket shelves.
3. Product Messaging:
- 1st priority: Product Name
- 2nd priority: Nutritional call outs (All natural, GF, Vegan, High Fibre, No added sugar, etc.). This info is available in the current packaging and more info on the website.
- 3rd priority: Ingredients on front cover (example: 7 ingredients only: x1, x2, x3, x4, x5, x6, x7.)
- 4th priority: Locally Made by a nutritionist.
- 5th priority: Sugar content in the nutritional panel to say: From Healthy Natural Sources
Tips:
1. Use Style 1 as benchmark.
2. Use the other image references as follows:
Style 2 and 5 = Try do something similar for the energy ball bags.
Style 4 = Maybe add the line up of other flavours on the back or the side of the packaging for the energy ball box and the cereal bags.
Style 7 = Do something similar with regards to the use of real imagery on the packaging as if you can pick out the product right of the packaging. Note also how they list the ingredients on the front of packaging.
Style 8 = Do something similar - be proud about the real ingredients used.
Style 9 = An example of how much transparent area we can do, please suggest a nice unique transparent shape.
Style 10 = copy the way it communicates the health benefits very clearly.

```html
<!DOCTYPE html>
<html lang="en">
<head>
<meta charset="utf-8">
<title>Maple &amp; Vanilla Granola – Packaging Range</title>
<link href="https://fonts.googleapis.com/css2?family=Oswald:wght@500;600&family=Arimo:wght@400;700&display=swap" rel="stylesheet">
<style>
:root{
  --stage:#f1f1f1;
  --pink:#de4b9b;
  --pink-deep:#c93585;
  --plum:#7e1f51;
  --gold-a:#c89a4b;
  --gold-b:#f2dc9c;
  --cream:#f7ecc7;
  --ink:#141014;
  --white:#ffffff;
  --illo-a:#f3e1b4;
  --illo-b:#9a5a3a;
}
*{box-sizing:border-box;margin:0;padding:0}
html,body{width:1200px;height:720px;overflow:hidden}
body{background:var(--stage);font-family:"Arimo",Arial,sans-serif;color:var(--ink);position:relative}
.piece{position:absolute;background:var(--pink);overflow:hidden}
.title{font-family:"Oswald","Arial Narrow",sans-serif;font-weight:600;line-height:.95;text-transform:uppercase;color:var(--ink)}
.brand{font-family:"Oswald","Arial Narrow",sans-serif;font-weight:600;color:var(--ink);text-transform:uppercase;letter-spacing:.04em;line-height:1}
.sub{font-size:7px;text-transform:uppercase;letter-spacing:.02em}
.gold{background:linear-gradient(100deg,var(--gold-a),var(--gold-b) 45%,var(--gold-a))}
.seal{position:absolute;border-radius:50%;background:radial-gradient(circle at 35% 30%,#fff,#bbb 60%,#777);border:2px solid #555}
.illo{position:absolute;border-radius:45% 55% 50% 40%;background:radial-gradient(circle at 40% 40%,var(--illo-a),#e9c98a 50%,var(--illo-b))}
.claims{position:absolute;display:flex;gap:10px}
.claim{display:flex;flex-direction:column;align-items:center;font-size:10px;line-height:1.05;text-align:center;color:var(--ink)}
.claim svg{margin-bottom:3px}
.net{position:absolute;font-weight:700;font-size:12px}

/* cereal bag */
.cereal-bag{left:40px;top:60px;width:390px;height:600px;border-radius:26px 26px 6px 6px}
.cereal-bag .label{position:absolute;left:36px;top:70px;width:318px;height:170px;border-radius:8px}
.cereal-bag .seal{left:10px;top:40px;width:50px;height:50px}
.cereal-bag .brand{position:absolute;left:14px;top:100px;font-size:15px;width:100px}
.cereal-bag .title{position:absolute;left:118px;top:14px;font-size:46px}
.cereal-bag .sub{position:absolute;left:70px;top:152px}
.cereal-bag .base{position:absolute;left:18px;top:400px;width:354px;height:200px;background:var(--white);border-radius:24px 24px 0 0}
.cereal-bag .window{position:absolute;left:46px;top:270px;width:298px;height:230px;background:var(--plum);border:3px solid var(--ink);border-radius:30px 30px 40px 40px / 20px 20px 60px 60px}
.cereal-bag .illo{left:30px;top:430px;width:150px;height:150px}
.cereal-bag .claims{left:200px;top:520px}
.cereal-bag .net{left:250px;top:570px}

/* energy ball wrapper */
.wrapper{left:470px;top:70px;width:380px;height:580px;border-radius:22px}
.wrapper .flip{position:absolute;left:20px;top:12px;width:340px;transform:rotate(180deg);text-align:center;height:150px;display:flex;flex-direction:column-reverse;gap:5px}
.wrapper .handles{display:flex;justify-content:center;gap:10px}
.wrapper .handle{background:var(--white);border-radius:10px;padding:2px 10px;font-size:8px;font-weight:700}
.wrapper .join{font-family:"Oswald",sans-serif;font-weight:500;font-size:12px;text-transform:uppercase;line-height:1.1}
.wrapper .blurb{font-size:7px;text-transform:uppercase;line-height:1.3}
.wrapper .band{position:absolute;left:0;top:200px;width:380px;height:124px}
.wrapper .seal{left:80px;top:-8px;width:52px;height:52px}
.wrapper .brand{position:absolute;left:140px;top:88px;font-size:13px}
.wrapper .title{position:absolute;left:222px;top:8px;font-size:36px}
.wrapper .sub{position:absolute;left:222px;top:112px;font-size:6px}
.wrapper .illo{left:-20px;top:300px;width:150px;height:150px}
.wrapper .claims{left:140px;top:338px}
.wrapper .net{left:290px;top:392px}
.wrapper .panel{position:absolute;left:30px;top:430px;width:320px;height:120px;background:var(--white);border-radius:8px;padding:8px;display:flex;gap:10px;font-size:5.5px;line-height:1.35}
.nip{width:150px;border-collapse:collapse}
.nip th,.nip td{border-bottom:.5px solid #999;padding:1px 2px;text-align:left;font-weight:400}
.nip th{font-weight:700}
.wrapper .facts b{display:block;font-size:6px;margin-bottom:2px}
.wrapper .facts p{margin-bottom:4px}
.origin{display:flex;gap:4px;align-items:center;border:1px solid #2a8a3a;padding:2px;font-weight:700}
.origin span{width:12px;height:12px;background:#2a8a3a;display:block}

/* display box */
.box-lid{left:890px;top:70px;width:270px;height:260px;border-radius:4px}
.box-lid .label{position:absolute;left:24px;top:24px;width:228px;height:130px;border-radius:8px}
.box-lid .seal{left:-12px;top:-14px;width:40px;height:40px}
.box-lid .brand{position:absolute;left:10px;top:82px;font-size:11px}
.box-lid .title{position:absolute;left:92px;top:10px;font-size:34px}
.box-lid .sub{position:absolute;left:40px;top:118px;font-size:6px}
.box-lid .note{position:absolute;left:10px;top:166px;width:250px;height:90px;background:var(--white);border-radius:4px}
.box-lid .illo{left:6px;top:6px;width:70px;height:76px}
.box-lid .copy{position:absolute;left:84px;top:10px;font-size:7px;text-transform:uppercase;line-height:1.3}
.box-front{left:890px;top:360px;width:270px;height:290px;border-radius:4px}
.box-front .strip{position:absolute;left:0;top:150px;width:270px;height:140px;background:var(--white)}
.box-front .disc{position:absolute;left:18px;top:30px;width:80px;height:80px;border-radius:50%}
.box-front .brand{position:absolute;left:14px;top:118px;font-size:12px}
.box-front .title{position:absolute;left:104px;top:18px;font-size:38px}
.box-front .sub{position:absolute;left:104px;top:150px;font-size:6px}
.box-front .claims{left:24px;top:190px}
.box-front .net{left:190px;top:256px}
</style>
</head>
<body>

<!-- Cereal bag front -->
<section class="piece cereal-bag">
  <div class="label gold">
    <div class="seal"></div>
    <div class="brand">Wren Nutrition</div>
    <h1 class="title">Maple &amp;<br>Vanilla<br>Granola</h1>
    <p class="sub">With coconut &amp; dried cranberries</p>
  </div>
  <div class="base"></div>
  <div class="window" role="img" aria-label="Clear window showing the granola inside"></div>
  <div class="illo" role="img" aria-label="Illustration of vanilla flower, pods, apricot, almonds and cranberries"></div>
  <div class="claims">
    <div class="claim"><svg width="18" height="18" viewBox="0 0 18 18"><circle cx="9" cy="9" r="8" fill="none" stroke="#141014" stroke-width="1.6"/><ellipse cx="9" cy="9" rx="3" ry="5" fill="#141014"/></svg>High<br>Fiber</div>
    <div class="claim"><svg width="18" height="18" viewBox="0 0 18 18"><circle cx="9" cy="9" r="8" fill="none" stroke="#141014" stroke-width="1.6"/><path d="M9 4v10M6 7l3 2 3-2M6 10l3 2 3-2" fill="none" stroke="#141014" stroke-width="1.3"/></svg>Gluten<br>Free</div>
    <div class="claim"><svg width="18" height="18" viewBox="0 0 18 18"><circle cx="9" cy="9" r="8" fill="none" stroke="#141014" stroke-width="1.6"/><path d="M5 12c0-5 4-7 8-7-1 5-4 7-8 7z" fill="#141014"/></svg>Vegan</div>
    <div class="claim"><svg width="18" height="18" viewBox="0 0 18 18"><circle cx="9" cy="9" r="8" fill="none" stroke="#141014" stroke-width="1.6"/><rect x="6" y="6" width="6" height="6" fill="#141014"/><path d="M4 14L14 4" stroke="#141014" stroke-width="1.3"/></svg>No Added<br>Sugar</div>
  </div>
  <p class="net">630G NET</p>
</section>

<!-- Energy ball wrapper, flat -->
<section class="piece wrapper">
  <div class="flip">
    <div class="handles"><span class="handle">@wrenkitchen</span><span class="handle">@wrennutrition</span></div>
    <p class="join">Join us in the kitchen &amp;<br>view more healthy recipes:</p>
    <p class="blurb">Made in small batches, &amp; full of fibre, these energy<br>balls make for a deliciously healthy snack.</p>
    <p class="blurb">Sweet, chewy &amp; delicious, our apricot &amp; coconut<br>energy balls are filled with dried apricots, almonds,<br>coconut &amp; a touch of maple syrup &amp; vanilla.</p>
  </div>
  <div class="band gold">
    <div class="seal"></div>
    <div class="brand">Wren Nutrition</div>
    <h2 class="title">Maple &amp;<br>Vanilla<br>Granola</h2>
    <p class="sub">With coconut &amp; dried cranberries</p>
  </div>
  <div class="illo" role="img" aria-label="Illustration of vanilla flower, apricot slice, walnut and almonds"></div>
  <div class="claims">
    <div class="claim"><svg width="20" height="20" viewBox="0 0 18 18"><circle cx="9" cy="9" r="8" fill="none" stroke="#141014" stroke-width="1.6"/><ellipse cx="9" cy="9" rx="3" ry="5" fill="#141014"/></svg>High<br>Fiber</div>
    <div class="claim"><svg width="20" height="20" viewBox="0 0 18 18"><circle cx="9" cy="9" r="8" fill="none" stroke="#141014" stroke-width="1.6"/><path d="M9 4v10M6 7l3 2 3-2M6 10l3 2 3-2" fill="none" stroke="#141014" stroke-width="1.3"/></svg>Gluten<br>Free</div>
    <div class="claim"><svg width="20" height="20" viewBox="0 0 18 18"><circle cx="9" cy="9" r="8" fill="none" stroke="#141014" stroke-width="1.6"/><path d="M5 12c0-5 4-7 8-7-1 5-4 7-8 7z" fill="#141014"/></svg>Vegan</div>
    <div class="claim"><svg width="20" height="20" viewBox="0 0 18 18"><circle cx="9" cy="9" r="8" fill="none" stroke="#141014" stroke-width="1.6"/><rect x="6" y="6" width="6" height="6" fill="#141014"/><path d="M4 14L14 4" stroke="#141014" stroke-width="1.3"/></svg>No Added<br>Sugar</div>
  </div>
  <p class="net">40G NET</p>
  <div class="panel">
    <table class="nip">
      <tr><th colspan="3">The goodness you're receiving</th></tr>
      <tr><th></th><th>Per serve</th><th>Per 100g</th></tr>
      <tr><td>Energy</td><td>752kJ</td><td>1880kJ</td></tr>
      <tr><td>Protein</td><td>3.5g</td><td>8.8g</td></tr>
      <tr><td>Fat, total</td><td>13.2g</td><td>33.0g</td></tr>
      <tr><td>– Saturated</td><td>6.7g</td><td>16.7g</td></tr>
      <tr><td>Carbohydrate</td><td>9.9g</td><td>24.8g</td></tr>
      <tr><td>– Sugars</td><td>9.7g</td><td>24.2g</td></tr>
      <tr><td>Dietary fibre</td><td>5.6g</td><td>14g</td></tr>
      <tr><td>Sodium</td><td>8mg</td><td>20mg</td></tr>
    </table>
    <div class="facts">
      <b>The goodness you're eating</b>
      <p>Dried apricot (37%), almond meal (25%), desiccated coconut (25%), maple syrup (7%), coconut oil (1%), vanilla extract (1%).</p>
      <p>Made with love in Canberra, Australia</p>
      <p>Store in a cool, dry place and out of direct sunlight</p>
      <div class="origin"><span></span>Made in Australia from at least 30% Australian ingredients</div>
      <p>Wren Nutrition<br>14 Larkin Lane, Forrest ACT 2603</p>
    </div>
  </div>
</section>

<!-- Display box lid -->
<section class="piece box-lid">
  <div class="label gold">
    <div class="seal"></div>
    <div class="brand">Wren Nutrition</div>
    <h2 class="title">Maple &amp;<br>Vanilla<br>Granola</h2>
    <p class="sub">With coconut &amp; dried cranberries</p>
  </div>
  <div class="note">
    <div class="illo" role="img" aria-label="Illustration of apricot, vanilla flower and nuts"></div>
    <p class="copy">Sweet, chewy &amp; delicious, our apricot &amp; coconut energy balls are filled with dried apricots, almonds, coconut &amp; a touch of maple syrup &amp; vanilla.<br><br>Made in small batches, &amp; full of fibre, these energy balls make for a deliciously healthy snack.</p>
  </div>
</section>

<!-- Display box front -->
<section class="piece box-front">
  <div class="strip"></div>
  <div class="disc gold"></div>
  <div class="brand">Wren Nutrition</div>
  <h2 class="title">Maple &amp;<br>Vanilla<br>Granola</h2>
  <p class="sub">With coconut &amp; dried cranberries</p>
  <div class="claims">
    <div class="claim"><svg width="20" height="20" viewBox="0 0 18 18"><circle cx="9" cy="9" r="8" fill="none" stroke="#141014" stroke-width="1.6"/><ellipse cx="9" cy="9" rx="3" ry="5" fill="#141014"/></svg>High<br>Fiber</div>
    <div class="claim"><svg width="20" height="20" viewBox="0 0 18 18"><circle cx="9" cy="9" r="8" fill="none" stroke="#141014" stroke-width="1.6"/><path d="M9 4v10M6 7l3 2 3-2M6 10l3 2 3-2" fill="none" stroke="#141014" stroke-width="1.3"/></svg>Gluten<br>Free</div>
    <div class="claim"><svg width="20" height="20" viewBox="0 0 18 18"><circle cx="9" cy="9" r="8" fill="none" stroke="#141014" stroke-width="1.6"/><path d="M5 12c0-5 4-7 8-7-1 5-4 7-8 7z" fill="#141014"/></svg>Vegan</div>
    <div class="claim"><svg width="20" height="20" viewBox="0 0 18 18"><circle cx="9" cy="9" r="8" fill="none" stroke="#141014" stroke-width="1.6"/><rect x="6" y="6" width="6" height="6" fill="#141014"/><path d="M4 14L14 4" stroke="#141014" stroke-width="1.3"/></svg>No Added<br>Sugar</div>
  </div>
  <p class="net">40G NET</p>
</section>

</body>
</html>
```